VocaTerrana Community/ Talent Gallery

VocaTerrana is developing a collaborative career course, with coaching and community exchange. Goal is to offer a platform where talented candidates can show their expertise and find projects, partners, and develop their online portfolios!

Here is a good example of the type of thing we hope to create with focus on sustainability focused talent to task matching
http://www.brambleforth.com/global-themes/employment-and-growth/connecting-talent-with-opportunity-in-the-digital-age

We hope to have a "grid style" gallery where it is easy to search by talent types and focus areas within the scope of "Sustainability" issues...Food/Water/Energy, Public Health, Technology, Sustainable Cities, Infrastructure, Education, Policy, Emerging Economies, Ecosystems, Social Innovation, inclusive Security, Equity Issues. For each topic/ header we hope to have candidates post their completed portfolios to exhibit resumes, biography, a case study... they may actually prepare these on other sites, but can link in OR alternately that they can easily create here, similar to "pinqo.io" ....

Hope to include a blog space titled "Rising over the Rift", where people can mix it up across these topic issues as they are interdependent and often require partners across discipline areas! If possible another area where jobs related to these issues may be posted as project or job opportunities by potential employers.

If there is a way to create a feed from various job sites that already exist...like Jobora...or http://www.greenledgerworks.com/ that would be super great. Again...sort of a portal connection to bridge the gap ....instead of candidates having to search all the time, we are hoping they can advertise their talent and employers may search here for these well presented portfolios!

Target Market(s)

Educators, Students, Career Transitioners, Employers, Professional Associations, Talent Recruiters with focus on Sustainability related Talent to Task matching!

Industry/Entity Type

Sustainability

Number of Pages Required

4 page

Font styles to use
Sans Serif

Colors
3176b5
32b8a4
add136

Requirements
Must have
• Not sure about the coded/ uncoded option here....
• Must have - grid style area where Sustainability Professionals with varied focus areas can exhibit their talent portfolios
• appear as a Talent Gallery that starts with photos & obvious organization...other tabs to be in a menu.
• ability to search both talent and task opportunity areas to help coaches or community members make matches....some topic focused category or tag words to help make them searchable...???
• consistent professional styling to existing website and new artflock postcard shared in brief/ images area
• Interactive blog space where articles, issues may be posted, discussed
• Bulletin board or feed for project opportunities to be posted where candidates may locate them and/or employers may express specific "call" for talent..These may be Short term Internships, Projects, Consulting Team Opportunity, or Jobs/ part time to full time....
Nice to have
• A calendar area where we can post networking opportunities, issues presentations where potential partners can meet the next generation leaders, attend a forum or webinar presentation.
Should not have
• Too much text on front page...Should be clean design,

```html
<!DOCTYPE html>
<html lang="en">
<head>
<meta charset="utf-8">
<title>VocaTerrana – Collaborative Career Course</title>
<link href="https://fonts.googleapis.com/css2?family=Raleway:wght@400;500;600;700&family=Open+Sans:ital,wght@0,400;0,600;0,700;1,400&display=swap" rel="stylesheet">
<style>
:root{
  --blue:#2c60aa;
  --blue-dark:#224f8f;
  --green:#9bc832;
  --green-dark:#85b024;
  --teal:#32b8a4;
  --ink:#333;
  --muted:#777;
  --line:#e4e4e4;
  --footer:#202020;
  --footer-bottom:#141414;
  --footer-text:#b8b8b8;
  --gold:#f2b01e;
}
*{box-sizing:border-box;margin:0;padding:0}
html,body{width:1200px;height:2497px;overflow:hidden}
body{position:relative;background:#fff;font-family:"Open Sans",Arial,sans-serif;color:var(--ink)}
.abs{position:absolute}
.raleway{font-family:"Raleway",Arial,sans-serif}

/* header */
.site-header{position:absolute;left:0;top:0;width:1200px;height:131px;background:#fff;box-shadow:0 2px 4px rgba(0,0,0,.08);z-index:2}
.brand{position:absolute;left:100px;top:40px;display:flex;align-items:center;gap:14px}
.brand-dot{width:52px;height:52px;border-radius:50%;background:var(--blue)}
.brand-name{font-family:"Raleway",Arial,sans-serif;font-weight:600;font-size:27px;color:var(--blue);letter-spacing:.5px}
.nav a{position:absolute;top:0;height:131px;line-height:131px;font-family:"Raleway",Arial,sans-serif;font-size:13px;color:#333;text-decoration:none}
.nav .active{left:500px;width:96px;background:var(--blue);color:#fff;text-align:center}
.login{position:absolute;left:1005px;top:47px;width:95px;height:36px;background:var(--blue);color:#fff;font-size:13px;display:flex;align-items:center;justify-content:center;gap:7px;border-radius:2px}

/* hero */
.hero{position:absolute;left:0;top:131px;width:1200px;height:526px;background:linear-gradient(120deg,#2f2d2b 0%,#57524c 28%,#9c968c 52%,#c9c5bd 62%,#5e5750 80%,#2e2a27 100%)}
.hero-shade{position:absolute;inset:0;background:linear-gradient(90deg,rgba(0,0,0,.35),rgba(0,0,0,.05) 60%,rgba(0,0,0,.2))}
.hero-ring{position:absolute;left:158px;top:110px;width:300px;height:300px;border-radius:50%;background:rgba(255,255,255,.1)}
.hero-kicker{position:absolute;left:200px;top:206px;font-family:"Raleway",Arial,sans-serif;font-size:27px;color:var(--green)}
.hero-title{position:absolute;left:98px;top:240px;font-family:"Raleway",Arial,sans-serif;font-weight:600;font-size:46px;color:#fff;letter-spacing:.5px}
.search-panel{position:absolute;left:810px;top:69px;width:292px;height:366px;background:rgba(20,20,20,.82)}
.search-head{height:53px;background:var(--green);color:#fff;font-family:"Raleway",Arial,sans-serif;font-weight:700;font-size:15px;text-align:center;line-height:53px;letter-spacing:.5px}
.field{position:absolute;left:24px;width:244px;height:33px;background:#fff;font-size:11px;color:#555;padding-left:12px;line-height:33px}
.field.select::after{content:"";position:absolute;right:12px;top:12px;width:6px;height:6px;border-right:1.5px solid #555;border-bottom:1.5px solid #555;transform:rotate(45deg)}
.search-btn{position:absolute;left:24px;top:289px;width:240px;height:38px;background:var(--blue);color:#fff;font-weight:600;font-size:13px;display:flex;align-items:center;justify-content:center;gap:10px}

/* phases */
.phases-title{position:absolute;top:696px;width:1200px;text-align:center;font-family:"Raleway",Arial,sans-serif;font-size:26px;color:#333}
.phases-intro{position:absolute;left:100px;top:742px;width:1000px;text-align:center;font-size:12.5px;line-height:25px;color:#555}
.phase{position:absolute;top:817px;width:240px;text-align:center}
.phase-ring{width:144px;height:144px;margin:0 auto;border-radius:50%;border:2px solid var(--blue);display:flex;align-items:center;justify-content:center}
.phase-disc{width:122px;height:122px;border-radius:50%;background:var(--blue);display:flex;align-items:center;justify-content:center}
.phase.green .phase-ring{border-color:var(--green)}
.phase.green .phase-disc{background:var(--green)}
.phase-name{margin-top:12px;font-family:"Raleway",Arial,sans-serif;font-weight:600;font-size:15px;color:var(--blue)}
.phase.green .phase-name{color:var(--green)}
.phase-text{margin-top:8px;font-size:11.5px;line-height:23px;font-style:italic;color:var(--muted)}

/* apply band */
.apply{position:absolute;left:0;top:1112px;width:1200px;height:286px;background:linear-gradient(100deg,#2b2b25,#3d3c33 40%,#2f3029 70%,#26261f)}
.apply-shade{position:absolute;inset:0;background:rgba(0,0,0,.45)}
.apply-title{position:absolute;top:60px;width:1200px;text-align:center;font-family:"Raleway",Arial,sans-serif;font-size:26px;color:#fff}
.apply-text{position:absolute;left:130px;top:102px;width:940px;text-align:center;font-size:11.5px;line-height:22px;color:#e8e8e8}
.apply-input{position:absolute;left:178px;top:178px;width:679px;height:45px;background:#fff;font-size:11.5px;font-style:italic;color:#888;padding-left:18px;line-height:45px}
.apply-btn{position:absolute;left:865px;top:178px;width:155px;height:45px;background:var(--green);color:#fff;font-size:14px;text-align:center;line-height:45px}

/* blog */
.blog-title{position:absolute;left:98px;top:1447px;font-family:"Raleway",Arial,sans-serif;font-size:26px;color:#333}
.pager{position:absolute;top:1454px;width:19px;height:19px;border:1px solid #ccc;display:flex;align-items:center;justify-content:center}
.blog-rule{position:absolute;left:98px;top:1493px;width:627px;height:1px;background:var(--line)}
.post{position:absolute;left:98px;width:627px;height:172px}
.post-photo{position:absolute;left:4px;top:0;width:169px;height:136px;border:3px solid #fff;box-shadow:0 0 0 1px #ddd}
.post-title{position:absolute;left:207px;top:-2px;font-family:"Raleway",Arial,sans-serif;font-weight:600;font-size:14px;color:#222}
.post-meta{position:absolute;left:207px;top:20px;font-size:11px;color:var(--green-dark)}
.post-text{position:absolute;left:207px;top:42px;width:420px;font-size:11px;line-height:22.5px;color:#666}
.post-foot{position:absolute;left:207px;top:119px;display:flex;align-items:center}
.stars{color:var(--gold);font-size:13px;letter-spacing:1px}
.stars .off{color:#999}
.divider{width:1px;height:16px;background:#ccc;margin:0 10px}
.tag{height:23px;line-height:21px;font-size:11px;padding:0 13px;border:1px solid;margin-right:8px}
.tag.resume{border-color:var(--blue);color:var(--blue);width:83px;text-align:center;padding:0}
.tag.bio{border-color:var(--green);color:var(--green-dark);width:78px;text-align:center;padding:0}
.tag.case{border-color:var(--teal);color:var(--teal);width:80px;text-align:center;padding:0}
.post-sep{position:absolute;left:98px;width:627px;height:1px;background:var(--line)}

/* sidebar */
.side-card{position:absolute;left:785px;top:1449px;width:315px;height:282px;border:1px solid var(--line);background:#fff}
.side-title{position:absolute;top:22px;width:100%;text-align:center;font-family:"Raleway",Arial,sans-serif;font-size:16px;color:#333}
.calendar{position:absolute;left:24px;top:68px;width:267px;height:204px;border:1px solid #ddd}
.cal-head{height:33px;display:flex;align-items:center;justify-content:space-between;border-bottom:1px solid #ddd}
.cal-arrow{width:17px;height:33px;background:var(--blue);display:flex;align-items:center;justify-content:center}
.cal-month{font-size:11px;color:var(--blue);font-weight:600;letter-spacing:.5px}
.cal-grid{display:grid;grid-template-columns:repeat(7,32px);gap:2px;padding:8px 0 0 11px}
.cal-grid span{height:23px;font-size:8.5px;text-align:center;line-height:23px;color:#444;border:1px solid #e2e2e2}
.cal-grid .dow{border:none;font-weight:700;height:16px;line-height:16px}
.cal-grid .hot{background:var(--green);color:#fff;border-color:var(--green)}
.cal-grid .dim{color:#bbb}
.event-card{position:absolute;left:785px;top:1751px;width:315px;height:312px;background:#f6f6f6;border:1px solid #ececec}
.event-lead{position:absolute;left:25px;top:27px;width:265px;text-align:center;font-size:12.5px;line-height:25px;color:#333;font-weight:600}
.event-text{position:absolute;left:25px;top:85px;width:265px;text-align:center;font-size:11px;line-height:22.5px;color:#666}
.event-btn{position:absolute;left:47px;top:241px;width:221px;height:40px;background:var(--green);color:#fff;font-weight:600;font-size:13px;text-align:center;line-height:40px}

/* newsletter */
.newsletter{position:absolute;left:0;top:2115px;width:1200px;height:100px;background:var(--green)}
.nl-icon{position:absolute;left:98px;top:24px}
.nl-kicker{position:absolute;left:226px;top:20px;font-family:"Raleway",Arial,sans-serif;font-size:15px;color:#fff;font-weight:600}
.nl-title{position:absolute;left:226px;top:46px;font-family:"Raleway",Arial,sans-serif;font-size:28px;color:#fff;font-weight:700}
.nl-input{position:absolute;left:439px;top:30px;width:495px;height:42px;border-radius:21px;background:#fff;font-size:12px;color:#555;padding-left:22px;line-height:42px}
.nl-btn{position:absolute;left:945px;top:30px;width:155px;height:42px;border-radius:21px;background:var(--blue);color:#fff;font-weight:600;font-size:14px;text-align:center;line-height:42px}

/* footer */
.site-footer{position:absolute;left:0;top:2215px;width:1200px;height:218px;background:var(--footer)}
.f-head{position:absolute;font-family:"Raleway",Arial,sans-serif;font-weight:700;font-size:14px;color:#fff;letter-spacing:.3px}
.f-text{position:absolute;font-size:12px;line-height:21px;color:var(--footer-text)}
.f-row{position:absolute;display:flex;align-items:center;gap:14px;font-size:13px;color:var(--footer-text)}
.tweet{position:absolute;left:356px;width:240px;padding-left:35px;font-size:11px;line-height:21.5px;color:var(--footer-text)}
.tweet-mark{position:absolute;left:3px;top:4px;width:15px;height:15px;background:#ddd;border-radius:2px}
.update{position:absolute;left:637px;width:288px;border:1px solid #3a3a3a;padding:5px 14px;font-size:11px;line-height:21px;color:var(--footer-text)}
.update em{font-style:normal;color:var(--green)}
.social{position:absolute;left:993px;display:flex;align-items:center;gap:14px;font-size:12px;color:var(--footer-text)}
.social i{display:block;width:8px;height:8px;background:#fff}
.footer-bottom{position:absolute;left:0;top:2433px;width:1200px;height:64px;background:var(--footer-bottom);text-align:center;line-height:64px;font-size:11px;color:#ddd;letter-spacing:.3px}
</style>
</head>
<body>

<header class="site-header">
  <div class="brand"><span class="brand-dot"></span><span class="brand-name">VOCATERRANA</span></div>
  <nav class="nav">
    <a class="active" href="#">Home</a>
    <a style="left:626px" href="#">About</a>
    <a style="left:721px" href="#">Services</a>
    <a style="left:830px" href="#">Blog</a>
    <a style="left:916px" href="#">Contact</a>
  </nav>
  <div class="login">
    <svg width="10" height="12" viewBox="0 0 10 12"><rect x="0.5" y="5" width="9" height="6.5" fill="#fff"/><path d="M2.5 5V3.5a2.5 2.5 0 0 1 5 0V5" fill="none" stroke="#fff" stroke-width="1.4"/></svg>
    Log in
  </div>
</header>

<section class="hero">
  <div role="img" aria-label="Photo of a team of young professionals collaborating around a desk in a bright office" style="position:absolute;inset:0"></div>
  <div class="hero-shade"></div>
  <div class="hero-ring"></div>
  <div class="hero-kicker">Collaborative</div>
  <h1 class="hero-title">CAREER COURSE</h1>
  <form class="search-panel">
    <div class="search-head">SEARCH YOUR COMMUNITY</div>
    <div class="field" style="top:78px">Name*</div>
    <div class="field select" style="top:130px">Select Course*</div>
    <div class="field select" style="top:181px">Talent*</div>
    <div class="field select" style="top:233px">Task opportunity areas*</div>
    <div class="search-btn">Click to Search
      <svg width="13" height="13" viewBox="0 0 13 13"><circle cx="5.5" cy="5.5" r="4" fill="none" stroke="#fff" stroke-width="1.8"/><path d="M8.5 8.5L12 12" stroke="#fff" stroke-width="2"/></svg>
    </div>
  </form>
</section>

<h2 class="phases-title">Four Phase Career Course</h2>
<p class="phases-intro">Through a proven four-phase process, integrating principles of lifelong learning, career transitions, entrepreneurship, change management, and innovation, our interdisciplinary, collaborative course is designed to guide you through creative change for career, lifestyle and/or next generation leadership</p>

<div class="phase green" style="left:90px">
  <div class="phase-ring"><div class="phase-disc">
    <svg width="62" height="62" viewBox="0 0 62 62"><circle cx="31" cy="31" r="24" fill="none" stroke="#fff" stroke-width="7"/><circle cx="31" cy="31" r="10" fill="none" stroke="#fff" stroke-width="5"/><path d="M14 14l9 9M48 14l-9 9M14 48l9-9M48 48l-9-9" stroke="#9bc832" stroke-width="5"/></svg>
  </div></div>
  <div class="phase-name">Clarify</div>
  <p class="phase-text">Architecto beatae vitae dicta sunt explicabo. sit aspernatur aut odit aut fugit, sed quia consequuntur magni dolores...</p>
</div>
<div class="phase" style="left:353px">
  <div class="phase-ring"><div class="phase-disc">
    <svg width="62" height="50" viewBox="0 0 62 50"><rect x="11" y="6" width="40" height="28" rx="2" fill="none" stroke="#fff" stroke-width="4"/><path d="M4 40h54v3a3 3 0 0 1-3 3H7a3 3 0 0 1-3-3z" fill="#fff"/></svg>
  </div></div>
  <div class="phase-name">Communicate</div>
  <p class="phase-text">Architecto beatae vitae dicta sunt explicabo. sit aspernatur aut odit aut fugit, sed quia consequuntur magni dolores...</p>
</div>
<div class="phase" style="left:614px">
  <div class="phase-ring"><div class="phase-disc">
    <svg width="56" height="56" viewBox="0 0 56 56"><path d="M44 20A18 18 0 0 0 12 18" fill="none" stroke="#fff" stroke-width="7"/><path d="M48 8v16H32z" fill="#fff"/><path d="M12 36a18 18 0 0 0 32 2" fill="none" stroke="#fff" stroke-width="7"/><path d="M8 48V32h16z" fill="#fff"/></svg>
  </div></div>
  <div class="phase-name">Collaborate</div>
  <p class="phase-text">Architecto beatae vitae dicta sunt explicabo. sit aspernatur aut odit aut fugit, sed quia consequuntur magni dolores...</p>
</div>
<div class="phase" style="left:877px">
  <div class="phase-ring"><div class="phase-disc">
    <svg width="58" height="58" viewBox="0 0 58 58"><path d="M30 10H12a4 4 0 0 0-4 4v32a4 4 0 0 0 4 4h32a4 4 0 0 0 4-4V28" fill="none" stroke="#fff" stroke-width="4"/><path d="M44 6l8 8-20 20-10 2 2-10z" fill="#fff"/></svg>
  </div></div>
  <div class="phase-name">Create</div>
  <p class="phase-text">Architecto beatae vitae dicta sunt explicabo. sit aspernatur aut odit aut fugit, sed quia consequuntur magni dolores...</p>
</div>

<section class="apply">
  <div role="img" aria-label="Photo of an audience seated at a community workshop" style="position:absolute;inset:0"></div>
  <div class="apply-shade"></div>
  <h2 class="apply-title">Apply to be a VocaTerrana</h2>
  <p class="apply-text">Accusantium doloremque laudantium, totam rem aperiam, eaque ipsa quae ab illo inventore veritatis et quasi architecto beatae vitae dicta sunt explicabo. Nemo enim ipsam voluptatem quia voluptas sit aspernatur aut odit aut fugit,dolorem ipsum quia dolor sit amet, consectetur, adipisci velit...</p>
  <div class="apply-input">Type Name of Course...</div>
  <div class="apply-btn">Click to Apply</div>
</section>

<h2 class="blog-title">Rising over the Rift</h2>
<div class="pager" style="left:679px"><svg width="6" height="8"><path d="M5 1L2 4l3 3" fill="none" stroke="#999" stroke-width="1.3"/></svg></div>
<div class="pager" style="left:703px"><svg width="6" height="8"><path d="M1 1l3 3-3 3" fill="none" stroke="#999" stroke-width="1.3"/></svg></div>
<div class="blog-rule"></div>

<article class="post" style="top:1528px">
  <div class="post-photo" role="img" aria-label="Photo of hands cupped around a globe" style="background:radial-gradient(circle at 50% 50%,#3a7fc0 0,#2b5f93 28%,#c99a78 32%,#a57357 60%,#e9e4dc 100%)"></div>
  <h3 class="post-title">Public Health</h3>
  <div class="post-meta">-by Marlo on May 15, 2016</div>
  <p class="post-text">TUt tortor elit, ullamcorper non odio sollicitudin, fermentum tristique nuncur abitur eu est orci. In sodales, dui eget tempor consequat.The standard rooms can be a bit small, as with historic hotel.&nbsp; But the...</p>
  <div class="post-foot"><span class="stars">★★★★<span class="off">★</span></span><span class="divider"></span><span class="tag resume">Resumes</span><span class="tag bio">Biography</span><span class="tag case">Case Study</span></div>
</article>
<div class="post-sep" style="top:1699px"></div>

<article class="post" style="top:1724px">
  <div class="post-photo" role="img" aria-label="Photo of a businessman holding a glowing digital tablet" style="background:linear-gradient(160deg,#15223a,#2d4a78 45%,#7fa6d2 60%,#1b2840)"></div>
  <h3 class="post-title">Technology</h3>
  <div class="post-meta">-by Marlo on May 15, 2016</div>
  <p class="post-text">TUt tortor elit, ullamcorper non odio sollicitudin, fermentum tristique nuncur abitur eu est orci. In sodales, dui eget tempor consequat.The standard rooms can be a bit small, as with historic hotel.&nbsp; But the...</p>
  <div class="post-foot"><span class="stars">★★★★<span class="off">★</span></span><span class="divider"></span><span class="tag resume">Resumes</span><span class="tag bio">Biography</span><span class="tag case">Case Study</span></div>
</article>
<div class="post-sep" style="top:1895px"></div>

<article class="post" style="top:1920px">
  <div class="post-photo" role="img" aria-label="Photo of a student writing at a desk in a classroom" style="background:linear-gradient(135deg,#d9c3a6,#a86d4b 40%,#e8ddd0 65%,#8a5a3e)"></div>
  <h3 class="post-title">Education</h3>
  <div class="post-meta">-by Marlo on May 15, 2016</div>
  <p class="post-text">TUt tortor elit, ullamcorper non odio sollicitudin, fermentum tristique nuncur abitur eu est orci. In sodales, dui eget tempor consequat.The standard rooms can be a bit small, as with historic hotel.&nbsp; But the...</p>
  <div class="post-foot"><span class="stars">★★★★<span class="off">★</span></span><span class="divider"></span><span class="tag resume">Resumes</span><span class="tag bio">Biography</span><span class="tag case">Case Study</span></div>
</article>

<aside class="side-card">
  <h3 class="side-title">Networking Opportunities Post</h3>
  <div class="calendar">
    <div class="cal-head">
      <span class="cal-arrow"><svg width="6" height="9"><path d="M5 1L1.5 4.5 5 8" fill="none" stroke="#fff" stroke-width="1.6"/></svg></span>
      <span class="cal-month">JUNE</span>
      <span class="cal-arrow"><svg width="6" height="9"><path d="M1 1l3.5 3.5L1 8" fill="none" stroke="#fff" stroke-width="1.6"/></svg></span>
    </div>
    <div class="cal-grid">
      <span class="dow">Mon</span><span class="dow">Tue</span><span class="dow">Wed</span><span class="dow">Thu</span><span class="dow">Fri</span><span class="dow">Sat</span><span class="dow">Sun</span>
      <span>1</span><span>2</span><span>3</span><span>4</span><span>5</span><span>6</span><span>7</span>
      <span>8</span><span>9</span><span>10</span><span>11</span><span>12</span><span>13</span><span>14</span>
      <span>15</span><span>16</span><span>17</span><span>18</span><span>19</span><span class="hot">20</span><span>21</span>
      <span>22</span><span>23</span><span>24</span><span>25</span><span>26</span><span>27</span><span>28</span>
      <span>29</span><span class="hot">30</span><span>31</span><span class="dim">1</span><span class="dim">2</span><span class="dim">3</span><span class="dim">4</span>
    </div>
  </div>
</aside>

<aside class="event-card">
  <p class="event-lead">Consequuntur magni dolores eos quiers ratione voluptatem sequi nesciunt.</p>
  <p class="event-text">Nemo enim ipsam voluptatem quia voluptas sit untur magni dolores eos qui ratione voluptatem dolorem ipsum quia dolor sit amet, consectetur, adipisci velit, sed quia non numquam eius modi aliquam quaerat voluptatem. Ut enim ad minima veniam, quis nostrum</p>
  <div class="event-btn">Meet On 20 June 2016</div>
</aside>

<section class="newsletter">
  <svg class="nl-icon" width="108" height="60" viewBox="0 0 108 60"><path d="M0 26L58 0l50 26-50 34z" fill="#8bb52a"/><path d="M0 26l58 34 50-34" fill="none" stroke="#a9d43f" stroke-width="2"/></svg>
  <div class="nl-kicker">Subscribe</div>
  <div class="nl-title">Newsletter :</div>
  <div class="nl-input">Enter Your Email Id :</div>
  <div class="nl-btn">Subscribe</div>
</section>

<footer class="site-footer">
  <h4 class="f-head" style="left:98px;top:32px">CONTACT US</h4>
  <p class="f-text" style="left:98px;top:55px">2270 Fernhollow Ave.<br>Millbrook, OR 97310 USA</p>
  <div class="f-row" style="left:98px;top:118px">
    <svg width="16" height="16" viewBox="0 0 16 16"><path d="M3 1l3 3-1.5 2c1 2 3 4 5 5L11.5 9.5l3 3L13 15C7 15 1 9 1 3z" fill="none" stroke="#ccc" stroke-width="1.2"/></svg>
    <span style="font-size:15px">(555) 014-2268</span>
  </div>
  <div class="f-row" style="left:98px;top:160px">
    <svg width="17" height="12" viewBox="0 0 17 12"><rect x=".6" y=".6" width="15.8" height="10.8" fill="none" stroke="#ccc" stroke-width="1.2"/><path d="M1 1l7.5 6L16 1" fill="none" stroke="#ccc" stroke-width="1.2"/></svg>
    <span>hello@vocaterrana.org</span>
  </div>

  <h4 class="f-head" style="left:356px;top:32px">LATEST TWEET`S</h4>
  <p class="tweet" style="top:58px"><span class="tweet-mark"></span>Good morning .... wherever you are today! All of us at ...See more here http://vt.link/q7Rd2Lm</p>
  <p class="tweet" style="top:130px"><span class="tweet-mark"></span>Good morning .... wherever you are today! All of us at ...See more here http://vt.link/q7Rd2Lm</p>

  <h4 class="f-head" style="left:637px;top:38px">RECENT UPDATES</h4>
  <p class="update" style="top:62px">Excepteur sint occaecat cupidatat non proident, sunt in culpa qui officia... <em>(23 May , 2016)</em></p>
  <p class="update" style="top:127px">Excepteur sint occaecat cupidatat non proident, sunt in culpa qui officia... <em>(23 May , 2016)</em></p>

  <h4 class="f-head" style="left:993px;top:32px">SOCIAL MEDIA</h4>
  <div class="social" style="top:62px"><i></i>Friendhall</div>
  <div class="social" style="top:90px"><i></i>Chirpline</div>
  <div class="social" style="top:118px"><i></i>Circlespace</div>
  <div class="social" style="top:147px"><i></i>Reelcast</div>
</footer>
<div class="footer-bottom">© 2016. VOCATERRANA |&nbsp; ALL RIGHTS RESERVED</div>

</body>
</html>
```